Social Media App Needs PPT Template

We need a PowerPoint template for a new social media company based in the DC area called "Bold Ledger." We provide an interactive digital platform for executives to share actionable advice. We would like to see designs that use our orange logo color as an accent, but are mainly grey, white, and black. The final design should communicate clean, chic, modern, and professional.

Target Market(s)

Executives

Industry/Entity Type

Information Technology

Font styles to use
Sans Serif

Colors
f78f20
fbe7d2
ffffff
000000
e8e8e8
757575

Requirements
Must have
• My project must have title page and many options for the body of the ppt (graphs, tables, etc). It also needs to be easy to modify. I must have someone who is experienced in creating powerpoint templates.
Nice to have
• It would be nice to have a very modern and clean design that includes the logo on every page, but still leaves a lot of room for the content of the slide
Should not have
• My design project should not look to busy.

```html
<!DOCTYPE html>
<html lang="en">
<head>
<meta charset="utf-8">
<title>Bold Ledger – Chart Slide</title>
<link href="https://fonts.googleapis.com/css2?family=Lato:wght@400;700&display=swap" rel="stylesheet">
<style>
  :root {
    --orange: #f49320;
    --navy: #222d3b;
    --graphite: #58595b;
    --silver: #cbcbcb;
    --body-grey: #757575;
    --backdrop: #cbcbcb;
    --white: #ffffff;
  }
  html, body {
    margin: 0;
    width: 1200px;
    height: 960px;
    overflow: hidden;
    background: var(--backdrop);
    font-family: "Lato", sans-serif;
  }
  .slide {
    position: absolute;
    left: 120px;
    top: 143px;
    width: 958px;
    height: 719px;
    background: var(--white);
  }
  .sidebar {
    position: absolute;
    left: 0; top: 0;
    width: 170px;
    height: 100%;
    background: var(--navy);
  }
  .brand {
    position: absolute;
    top: 70px;
    left: 0;
    width: 100%;
    text-align: center;
    color: var(--white);
    font-weight: 700;
    font-size: 24px;
    letter-spacing: 1px;
  }
  .brand-dot {
    display: block;
    width: 34px;
    height: 34px;
    margin: 0 auto 14px;
    border-radius: 50%;
    background: var(--orange);
  }
  .site {
    position: absolute;
    left: 19px;
    top: 671px;
    color: var(--white);
    font-size: 18px;
    line-height: 18px;
  }
  .slide-title {
    position: absolute;
    left: 205px;
    top: 98px;
    margin: 0;
    font-size: 41px;
    line-height: 41px;
    font-weight: 400;
    color: var(--orange);
  }
  .art {
    position: absolute;
    left: 0; top: 0;
  }
  .block-heading {
    position: absolute;
    margin: 0;
    font-size: 22px;
    line-height: 22px;
    font-weight: 700;
    white-space: nowrap;
  }
  .block-text {
    position: absolute;
    margin: 0;
    font-size: 16px;
    line-height: 23px;
    color: var(--body-grey);
    width: 230px;
  }
  .tone-graphite { color: var(--graphite); }
  .tone-orange { color: var(--orange); }
  .tone-navy { color: var(--navy); }
  .tone-silver { color: var(--silver); }
  .page-number {
    position: absolute;
    right: 36px;
    top: 684px;
    font-size: 13px;
    line-height: 13px;
    color: var(--body-grey);
  }
</style>
</head>
<body>
  <div class="slide">
    <aside class="sidebar">
      <div class="brand"><span class="brand-dot"></span>Bold Ledger</div>
      <div class="site">boldledger.com</div>
    </aside>

    <h1 class="slide-title">Title of the page</h1>

    <svg class="art" width="958" height="719" viewBox="0 0 958 719" aria-hidden="true">
      <line x1="205" y1="154" x2="921" y2="154" stroke="var(--orange)" stroke-width="1"/>

      <polyline points="208,231 443,231 500,296" fill="none" stroke="var(--graphite)" stroke-width="1.5"/>
      <polyline points="906,231 672,231 617,296" fill="none" stroke="var(--orange)" stroke-width="1.5"/>
      <polyline points="202,471 435,471 465,438" fill="none" stroke="var(--navy)" stroke-width="1.5"/>
      <polyline points="914,471 680,471 648,445" fill="none" stroke="var(--silver)" stroke-width="1.5"/>

      <g class="donut" stroke="var(--white)" stroke-width="2">
        <path d="M558,280 A106,106 0 0 1 664,386 L608,386 A50,50 0 0 0 558,336 Z" fill="var(--orange)"/>
        <path d="M664,386 A106,106 0 0 1 558,492 L558,436 A50,50 0 0 0 608,386 Z" fill="var(--silver)"/>
        <path d="M558,492 A106,106 0 0 1 452,386 L508,386 A50,50 0 0 0 558,436 Z" fill="var(--navy)"/>
        <path d="M452,386 A106,106 0 0 1 558,280 L558,336 A50,50 0 0 0 508,386 Z" fill="var(--graphite)"/>
      </g>
      <g font-family="Lato, sans-serif" font-size="19" fill="var(--white)" text-anchor="middle">
        <text x="506" y="342">25%</text>
        <text x="614" y="342">25%</text>
        <text x="506" y="449">25%</text>
        <text x="614" y="449">25%</text>
      </g>

      <line x1="802" y1="664" x2="926" y2="664" stroke="var(--navy)" stroke-width="1"/>
    </svg>

    <h2 class="block-heading tone-graphite" style="left:208px; top:205px;">NOBIS VIDENTUR</h2>
    <p class="block-text" style="left:208px; top:243px;">Lorem ipsum dolor sit amet, consectetuer adipi scing elit, sed diam nonummy nibh euismod tin.</p>

    <h2 class="block-heading tone-orange" style="left:678px; top:205px;">NOBIS VIDENTUR</h2>
    <p class="block-text" style="left:682px; top:243px;">Lorem ipsum dolor sit amet, consectetuer adipi scing elit, sed diam nonummy nibh euismod tin.</p>

    <h2 class="block-heading tone-navy" style="left:208px; top:437px;">NOBIS VIDENTUR</h2>
    <p class="block-text" style="left:208px; top:481px;">Lorem ipsum dolor sit amet, consectetuer adipi scing elit, sed diam nonummy nibh euismod tin.</p>

    <h2 class="block-heading tone-silver" style="left:691px; top:437px;">NOBIS VIDENTUR</h2>
    <p class="block-text" style="left:691px; top:481px;">Lorem ipsum dolor sit amet, consectetuer adipi scing elit, sed diam nonummy nibh euismod tin.</p>

    <div class="page-number">Page 5</div>
  </div>
</body>
</html>
```